"Harbor Builders" is a residential building company and needs a new business card design and may re

We would like a redesign based on the existing logo, and would like to see a new font as well. We are bespoke home builders who build sustainable energy efficient homes.

Industry/Entity Type

Construction

Contact Information for Business Card

Business card size 40mm x 90mm

Colors

Designer to choose colors to be used in the design.

```html
<!DOCTYPE html>
<html lang="en">
<head>
<meta charset="utf-8">
<title>Harbor Builders – Business Cards</title>
<link rel="stylesheet" href="https://fonts.googleapis.com/css2?family=Open+Sans:wght@400;600;700&display=swap">
<style>
  :root {
    --backdrop: #3b3430;
    --card: #141414;
    --card-edge: #1d1d1d;
    --white: #f2f2f2;
    --grey: #9a9a9a;
    --lime: #9bbf2e;
  }
  * { box-sizing: border-box; margin: 0; padding: 0; }
  html, body { width: 1200px; height: 864px; overflow: hidden; }
  body {
    background: var(--backdrop);
    font-family: "Open Sans", Arial, sans-serif;
    position: relative;
  }
  .card {
    position: absolute;
    width: 540px;
    height: 240px;
    background: linear-gradient(135deg, var(--card-edge), var(--card));
    box-shadow: 0 14px 30px rgba(0,0,0,0.45);
  }
  .card--front { left: 70px; top: 110px; }
  .card--back { left: 590px; top: 500px; }

  .wordmark {
    display: flex;
    align-items: center;
    gap: 14px;
  }
  .wordmark__square {
    width: 34px;
    height: 34px;
    background: var(--lime);
  }
  .wordmark__name {
    font-weight: 700;
    font-size: 34px;
    line-height: 1;
    color: var(--white);
    letter-spacing: -0.5px;
  }
  .card--front .wordmark { position: absolute; left: 80px; top: 80px; }
  .card--front .wordmark__name { color: #cfcfcf; }
  .front__url {
    position: absolute;
    left: 80px;
    top: 160px;
    font-size: 13px;
    letter-spacing: 3px;
    color: var(--grey);
  }

  .card--back .wordmark { position: absolute; left: 34px; top: 100px; }
  .card--back .wordmark__square { width: 22px; height: 22px; }
  .card--back .wordmark__name { font-size: 24px; }
  .back__divider {
    position: absolute;
    left: 284px;
    top: 30px;
    width: 1px;
    height: 180px;
    background: linear-gradient(to bottom, transparent, var(--grey) 30%, var(--grey) 70%, transparent);
  }
  .contact {
    position: absolute;
    left: 304px;
    top: 34px;
    color: var(--white);
    font-size: 12.5px;
    line-height: 1.38;
  }
  .contact__name {
    color: var(--lime);
    font-weight: 700;
    font-size: 14px;
    text-transform: uppercase;
    margin-bottom: 3px;
  }
  .contact__company { font-weight: 700; }
  .contact__line { display: flex; align-items: center; gap: 7px; }
  .contact__icon { width: 11px; height: 11px; flex: none; }
</style>
</head>
<body>
  <section class="card card--front">
    <div class="wordmark">
      <span class="wordmark__square"></span>
      <span class="wordmark__name">harbor builders</span>
    </div>
    <p class="front__url">www.harborbuilders.com.au</p>
  </section>

  <section class="card card--back">
    <div class="wordmark">
      <span class="wordmark__square"></span>
      <span class="wordmark__name">harbor builders</span>
    </div>
    <div class="back__divider"></div>
    <div class="contact">
      <p class="contact__name">Daniel Moretti</p>
      <p class="contact__company">Harbor Builders Pty Ltd</p>
      <p>PO Box 4120 Eastgate</p>
      <p>LPO Lakeside WA 6110</p>
      <p>Registration 30418</p>
      <p>ABN: 42 905 318 774</p>
      <p class="contact__line">
        <svg class="contact__icon" viewBox="0 0 12 12"><rect x="3" y="0.5" width="6" height="11" rx="1.2" fill="none" stroke="var(--lime)" stroke-width="1.4"/><circle cx="6" cy="9.3" r="0.8" fill="var(--lime)"/></svg>
        0400 118 736
      </p>
      <p class="contact__line">
        <svg class="contact__icon" viewBox="0 0 12 12"><rect x="0.5" y="2" width="11" height="8" fill="var(--lime)"/><path d="M0.5 2 L6 6.5 L11.5 2" fill="none" stroke="#141414" stroke-width="1"/></svg>
        daniel@harborbuilders.com.au
      </p>
      <p class="contact__line">
        <svg class="contact__icon" viewBox="0 0 12 12"><circle cx="6" cy="6" r="5.5" fill="var(--lime)"/><path d="M0.5 6 H11.5 M6 0.5 C3 3.5 3 8.5 6 11.5 M6 0.5 C9 3.5 9 8.5 6 11.5" fill="none" stroke="#141414" stroke-width="0.8"/></svg>
        www.harborbuilders.com.au
      </p>
    </div>
  </section>
</body>
</html>
```